Book Cover on Entrepreneurship for Eye Doctors

Book Title: The Lens Practice Builder: How to launch with confidence
Author: Rufus Tembley, Optom, MBA, DBA, EIC
I need a Book Cover with the following descriptions:
Topic: the book topic is entrepreneurship knowledge for eye care professionals.
The book's audience: eye care professionals who you know as Opticians, who sell eyeglasses and sunglasses;
Optometrists, test eyes, fit contact lenses, and prescribe medication
Ophthalmologists, perform eye surgery
More about the audience:
1- Young eye care professionals who don’t know about entrepreneurship and those who are stuck in the 9-to-5 job;
2- This is the first book written on entrepreneurship with eye care professionals in mind.
3- Private practice owners the established business guys who are looking to grow their business;
4- Many eye care professionals are MBA holders they may have learned a little bit about entrepreneurship during their MBA studies.
Use the sample cover above and the suggestions that follow as a guide:
1- The cover should be very simple leaving an empty space somewhere to sign the book;
2- The Title and author name should use a modern font;
3- The cover should provide info about what's inside the book through illustrations, for example:
a- Gears: illustrating entrepreneur growth mindset (or anything more explicit)
b- Spectacles, sunglasses, lenses, eye drops, or any other eye care-related correction tools illustrating eye care (or anything more explicit)
c- Symbols illustrating ideas, opportunity, and profit, like money, charts, light bulbs, brain, and coins,...(or anything more explicit)
d- Entrepreneurship illustrated by Briefcase, tie, suit,... (or anything more explicit)

The rest is your creativity and imagination interplay.

Target Market(s)

Eye care professionals: Opticians, Optometrists, Ophthalmologists, Eye Care Administrators, Students in eye specialties.

Industry/Entity Type

eye care

Requirements
Must have
• 1- The cover should be very simple leaving an empty space somewhere to sign the book; 2- The Title and author name should use a modern font; 3- The cover should provide info about what's inside the book through illustrations, for example: a- Gears: illustrating entrepreneur growth mindset (or anything more explicit) b- Spectacles, sunglasses, lenses, eye drops, or any other eye care-related correction tools illustrating eye care (or anything more explicit) c- Symbols illustrating ideas, opportunity, and profit, like money, charts, light bulbs, brain, and coins,...(or anything more explicit) d- Entrepreneurship illustrated by Briefcase, tie, suit,... (or anything more explicit)

```html
<!DOCTYPE html>
<html lang="en">
<head>
<meta charset="utf-8">
<title>The Lens Practice Builder — Book Cover</title>
<link rel="stylesheet" href="https://fonts.googleapis.com/css2?family=Bebas+Neue&display=swap">
<style>
  :root {
    --backdrop: #d4d4d4;
    --cover-black: #000000;
    --title-white: #ffffff;
    --accent-cyan: #00f6ff;
    --rule-cyan: #14c9d6;
    --iris-light: #8fc4ea;
    --iris-blue: #3f86c0;
    --iris-mid: #1f5a8a;
    --iris-deep: #0b2236;
  }
  * { margin: 0; padding: 0; box-sizing: border-box; }
  html, body {
    width: 1199px;
    height: 1200px;
    overflow: hidden;
    background: var(--backdrop);
  }
  .book-cover {
    position: absolute;
    left: 230px;
    top: 45px;
    width: 740px;
    height: 1110px;
    background: var(--cover-black);
    font-family: "Bebas Neue", "Arial Narrow", sans-serif;
    text-align: center;
  }
  .title {
    font-weight: 400;
  }
  .title-line {
    position: absolute;
    left: 0;
    right: 0;
    display: block;
    line-height: 1;
  }
  .title-line--lead {
    top: 58px;
    color: var(--title-white);
    font-size: 114px;
    letter-spacing: 1px;
  }
  .title-line--key {
    top: 165px;
    color: var(--accent-cyan);
    font-size: 122px;
    letter-spacing: 2px;
  }
  .subtitle {
    position: absolute;
    left: 158px;
    width: 424px;
    top: 341px;
    height: 56px;
    border-top: 1px solid var(--rule-cyan);
    border-bottom: 1px solid var(--rule-cyan);
    color: var(--title-white);
    font-size: 33px;
    letter-spacing: 1.5px;
    line-height: 56px;
  }
  .side-rule {
    position: absolute;
    left: 48px;
    top: 487px;
    width: 1px;
    height: 384px;
    background: #3a3a3a;
  }
  .eye-artwork {
    position: absolute;
    left: 62px;
    top: 505px;
    width: 616px;
    height: 352px;
  }
  .author {
    position: absolute;
    left: 0;
    right: 0;
    top: 1004px;
    color: var(--accent-cyan);
    font-size: 42px;
    letter-spacing: 1px;
  }
</style>
</head>
<body>
  <main class="book-cover">
    <h1 class="title">
      <span class="title-line title-line--lead">The Lens Practice</span>
      <span class="title-line title-line--key">BUILDER</span>
    </h1>
    <p class="subtitle">HOW TO LAUNCH WITH CONFIDENCE</p>
    <div class="side-rule"></div>
    <svg class="eye-artwork" viewBox="0 0 616 352" role="img" aria-label="Illustration of a glowing blue eye with fine light rays radiating outward">
      <defs>
        <radialGradient id="eye-glow" cx="50%" cy="50%" r="50%">
          <stop offset="0%" stop-color="var(--iris-light)" stop-opacity="1"/>
          <stop offset="22%" stop-color="var(--iris-blue)" stop-opacity="1"/>
          <stop offset="34%" stop-color="var(--iris-mid)" stop-opacity="0.9"/>
          <stop offset="65%" stop-color="var(--iris-mid)" stop-opacity="0.45"/>
          <stop offset="100%" stop-color="var(--iris-deep)" stop-opacity="0"/>
        </radialGradient>
      </defs>
      <ellipse cx="308" cy="176" rx="308" ry="176" fill="url(#eye-glow)"/>
    </svg>
    <p class="author">RUFUS TEMBLEY, OPTOM, MBA, DBA, EIC</p>
  </main>
</body>
</html>
```